Bork Ventures, Inc. Website redesign

Revamp the website, it is old and outdated. www.borkventuresinc.example

Target Market(s)

Information Technology Consulting and Staffing

Coding

Coded - Design and coding required

Number of Pages Required

5+ page

Colors

Designer to choose colors to be used in the design.

Requirements
Must have
• Outlined text boxes just like from the Tolvane.example site. A clean look

```html
<!DOCTYPE html>
<html lang="en">
<head>
<meta charset="utf-8">
<title>Bork Ventures, Inc.</title>
<link rel="stylesheet" href="https://fonts.googleapis.com/css2?family=Montserrat:wght@500;600;700;900&family=Lato:wght@400;700&family=Open+Sans:wght@400&display=swap">
<style>
:root{
  --brand:#8c1329;
  --brand-dark:#6e0f20;
  --ink:#333;
  --muted:#555;
  --page:#ffffff;
  --panel:#f4f4f4;
  --line:#dcdcdc;
}
*{box-sizing:border-box;margin:0;padding:0}
html,body{width:1200px;height:3524px;overflow:hidden;background:var(--page)}
body{position:relative;font-family:'Lato',sans-serif;color:var(--ink)}
.abs{position:absolute}

/* header */
.site-header{left:0;top:0;width:1200px;height:102px;background:#fff;border-bottom:1px solid #ccc;box-shadow:0 2px 4px rgba(0,0,0,.15);z-index:3}
.brand{display:flex;align-items:center;gap:10px;font-family:'Montserrat',sans-serif;font-weight:900;color:#222;letter-spacing:1px}
.brand .mark{width:28px;height:28px;background:var(--brand)}
.site-header .brand{position:absolute;left:112px;top:32px;font-size:30px}
.nav{position:absolute;left:0;top:40px;font-family:'Montserrat',sans-serif;font-size:15px;font-weight:500;color:var(--brand)}
.nav a{position:absolute;white-space:nowrap;color:inherit;text-decoration:none}
.nav svg{position:absolute;left:1076px;top:3px}

/* hero */
.hero{left:0;top:102px;width:1200px;height:597px;background:radial-gradient(ellipse at 50% 40%,#4d5e72 0%,#2d3a4b 55%,#1b2330 100%)}
.hero h1{position:absolute;left:0;width:1200px;top:178px;text-align:center;font-family:'Montserrat',sans-serif;font-weight:900;font-size:84px;color:#fff;letter-spacing:1px}
.hero p{position:absolute;left:0;width:1200px;top:288px;text-align:center;font-family:'Open Sans',sans-serif;font-size:24px;color:#fff}
.hero .arrow{position:absolute;top:276px}
.btn{display:inline-flex;align-items:center;justify-content:center;background:var(--brand);color:#fff;font-family:'Montserrat',sans-serif;font-weight:600;font-size:13.5px;text-transform:uppercase;text-decoration:none}
.hero .btn{position:absolute;left:528px;top:352px;width:142px;height:52px;font-size:14px}

/* services */
.services-band{left:0;top:699px;width:1200px;height:1230px;background:var(--panel)}
.card{position:absolute;background:#fff;border-top:4px solid var(--brand);box-shadow:0 1px 4px rgba(0,0,0,.25)}
.service{width:472px;height:581px}
.card .label{position:absolute;left:25px;top:21px;font-family:'Montserrat',sans-serif;font-weight:500;font-size:13.5px;color:#222}
.card .title{position:absolute;left:25px;top:51px;font-family:'Montserrat',sans-serif;font-weight:600;font-size:16px;color:var(--brand)}
.service .photo{position:absolute;left:0;top:103px;width:472px;height:226px}
.service .text{position:absolute;left:27px;top:355px;width:425px;font-size:13.5px;line-height:23px;color:var(--muted)}
.service .btn{position:absolute;left:27px;top:494px;width:133px;height:41px}

/* about */
.about-text{left:112px;top:1990px;width:400px;text-align:center;color:var(--brand)}
.about-text h2{font-family:'Montserrat',sans-serif;font-weight:500;font-size:26px;margin-bottom:22px}
.about-text p{font-size:14.5px;line-height:23px;margin-bottom:15px}
.about-text .btn{width:144px;height:42px;margin-top:42px;font-size:14px}
.about-photo{left:600px;top:1929px;width:600px;height:439px;background:linear-gradient(180deg,#6c7a8e 0%,#b59a86 32%,#4a4a52 60%,#2a2a30 100%)}

/* news */
.news-heading{left:110px;top:2437px;font-family:'Montserrat',sans-serif;font-weight:500;font-size:26px;color:var(--brand)}
.news{width:303px;height:307px}
.news .text{position:absolute;left:26px;top:112px;width:260px;font-size:13.5px;line-height:23px;color:var(--muted)}
.news .btn{position:absolute;left:26px;top:231px;width:127px;height:40px}

/* footer */
.footer-rule{left:0;top:3205px;width:1200px;height:1px;background:var(--line)}
.site-footer .brand{position:absolute;left:112px;top:3252px;font-size:26px}
.site-footer .brand .mark{width:24px;height:24px}
.address{left:112px;top:3308px;font-size:16px;line-height:22px;color:#333}
.address b,.office b{color:var(--brand);font-weight:700}
.address .indent{padding-left:68px}
.office{left:112px;top:3386px;font-size:16px}
.foot-head{font-family:'Montserrat',sans-serif;font-weight:500;font-size:18px;color:var(--brand)}
.foot-links{font-size:12.5px;color:#333;line-height:30px;list-style:none}
.social{display:flex;gap:10px}
.social span{width:33px;height:33px;border-radius:5px;background:var(--brand)}
.bottom-rule{left:0;top:3457px;width:1200px;height:1px;background:var(--line)}
.copyright{left:0;width:1200px;top:3479px;text-align:center;font-size:13px;color:#333}
.code{left:1128px;top:3479px;font-size:13px;color:#333}
</style>
</head>
<body>

<header class="site-header abs">
  <div class="brand"><span class="mark"></span>BORK VENTURES</div>
  <nav class="nav">
    <a style="left:458px">Home</a>
    <a style="left:545px">About us</a>
    <a style="left:652px">Services</a>
    <a style="left:754px">Strategy</a>
    <a style="left:857px">IT News</a>
    <a style="left:956px">Contact us</a>
    <svg width="14" height="14" viewBox="0 0 14 14" aria-label="Search"><circle cx="6" cy="6" r="4.2" fill="none" stroke="#8c1329" stroke-width="2"/><line x1="9" y1="9" x2="13" y2="13" stroke="#8c1329" stroke-width="2.2"/></svg>
  </nav>
</header>

<section class="hero abs" role="img" aria-label="Silhouettes of business people in front of a glowing digital globe network">
  <svg class="arrow" style="left:50px" width="16" height="32" viewBox="0 0 16 32"><polyline points="14,2 2,16 14,30" fill="none" stroke="#cfd6de" stroke-width="1.5"/></svg>
  <svg class="arrow" style="left:1128px;top:282px" width="16" height="32" viewBox="0 0 16 32"><polyline points="2,2 14,16 2,30" fill="none" stroke="#cfd6de" stroke-width="1.5"/></svg>
  <h1>BORK VENTURES</h1>
  <p>Bringing Thought Leadership and Quality to Every Project</p>
  <a class="btn">Read more</a>
</section>

<div class="services-band abs"></div>

<article class="card service" style="left:111px;top:657px">
  <div class="label">Hardware / Software Sales</div>
  <h3 class="title">Leveraging People Process and Technology</h3>
  <div class="photo" role="img" aria-label="Handshake over a desk with a laptop" style="background:linear-gradient(120deg,#9a9ea3 0%,#e6e6e4 45%,#f4f4f2 100%)"></div>
  <p class="text">We have access to multiple distributor partners throughout North America, as well as Elite Partner Status with many of the industry’s marquee manufacturers (such as Arvex) to ensure you are receiving the most aggressive pricing possible.</p>
  <a class="btn">Learn more</a>
</article>

<article class="card service" style="left:617px;top:657px">
  <div class="label">Professional Services</div>
  <h3 class="title">Leveraging People Process and Technology</h3>
  <div class="photo" role="img" aria-label="Engineer working on a laptop beside server racks" style="background:linear-gradient(90deg,#1e1e22 0%,#6e7076 35%,#2a2b30 60%,#8a8c92 100%)"></div>
  <p class="text">Our team provides experienced leadership and guidance, utilizing the industry standard methodologies. We help you maintain a compre-hensive view of strategy, governance, technology, people and process, to deliver more successful business outcomes.</p>
  <a class="btn">Learn more</a>
</article>

<article class="card service" style="left:111px;top:1272px">
  <div class="label">Technology Assessment</div>
  <h3 class="title">Leveraging People Process and Technology</h3>
  <div class="photo" role="img" aria-label="Two technicians checking equipment in a data center" style="background:linear-gradient(90deg,#d4d8de 0%,#9fa6b0 45%,#3a3c42 80%,#1e1f24 100%)"></div>
  <p class="text">Experience has shown companies that perform objective, third-party technology assessments have proven to be instrumental in identifying weaknesses or breaches in their environments before they adversely impact their business.</p>
  <a class="btn">Learn more</a>
</article>

<article class="card service" style="left:617px;top:1272px">
  <div class="label">Technology Consulting</div>
  <h3 class="title">Leveraging People Process and Technology</h3>
  <div class="photo" role="img" aria-label="Consultants meeting at a table in a bright office" style="background:linear-gradient(90deg,#7d8894 0%,#c9ced4 45%,#dfe3e7 70%,#5d6a78 100%)"></div>
  <p class="text">Implementing quality solutions is more than applying technology to problems. You need experts with deep technical knowledge and broad industry experience to help you design and implement cost-effective, reliable and secure solutions that meet your business priorities</p>
  <a class="btn">Learn more</a>
</article>

<section class="about-text abs">
  <h2>About Us</h2>
  <p>Bork Ventures, Inc. is an 8(a) innovative and rapidly growing full-service IT consulting firm. We provide our clients with cutting-edge technologies and the know-how to apply them to their individual business models.</p>
  <p>For over 20 + years, we have been providing reliable IT solutions to businesses in the Washington, DC Metro area and beyond.</p>
  <a class="btn">Read more</a>
</section>
<div class="about-photo abs" role="img" aria-label="Aerial view of a city at dusk with connected network lines"></div>

<h2 class="news-heading abs">Latest News</h2>

<article class="card news" style="left:112px;top:2491px">
  <div class="label">News 1 header</div><h3 class="title">Nostrud Exercitation Ullamco</h3>
  <p class="text">Lorem ipsum dolor sit amet, consectetur adipiscing elit, sed do eiusmod tempor incididunt ut labore et dolore</p>
  <a class="btn">Learn more</a>
</article>
<article class="card news" style="left:449px;top:2491px">
  <div class="label">News 2 header</div><h3 class="title">Architecto Beatae Vitae</h3>
  <p class="text">Lorem ipsum dolor sit amet, consectetur adipiscing elit, sed do eiusmod tempor incididunt ut labore et dolore</p>
  <a class="btn">Learn more</a>
</article>
<article class="card news" style="left:785px;top:2491px">
  <div class="label">News 3 header</div><h3 class="title">Necessitatibus Saepe Eveniet</h3>
  <p class="text">Lorem ipsum dolor sit amet, consectetur adipiscing elit, sed do eiusmod tempor incididunt ut labore et dolore</p>
  <a class="btn">Learn more</a>
</article>
<article class="card news" style="left:112px;top:2834px">
  <div class="label">News 4 header</div><h3 class="title">Finibus Bonorum et Malorum</h3>
  <p class="text">Lorem ipsum dolor sit amet, consectetur adipiscing elit, sed do eiusmod tempor incididunt ut labore et dolore</p>
  <a class="btn">Learn more</a>
</article>
<article class="card news" style="left:449px;top:2834px">
  <div class="label">News 5 header</div><h3 class="title">Finibus Bonorum et Malorum</h3>
  <p class="text">Lorem ipsum dolor sit amet, consectetur adipiscing elit, sed do eiusmod tempor incididunt ut labore et dolore</p>
  <a class="btn">Learn more</a>
</article>
<article class="card news" style="left:785px;top:2834px">
  <div class="label">News 6 header</div><h3 class="title">Finibus Bonorum et Malorum</h3>
  <p class="text">Lorem ipsum dolor sit amet, consectetur adipiscing elit, sed do eiusmod tempor incididunt ut labore et dolore</p>
  <a class="btn">Learn more</a>
</article>

<footer class="site-footer">
  <div class="footer-rule abs"></div>
  <div class="brand"><span class="mark"></span>BORK VENTURES</div>
  <p class="address abs"><b>Address:</b> Bork Ventures, Inc. 2208 Quillfield<br><span class="indent">Ct Halverton, MD 20990</span></p>
  <p class="office abs"><b>Office:</b>&nbsp; 301-555-0192</p>

  <h4 class="foot-head abs" style="left:559px;top:3250px">Links</h4>
  <ul class="foot-links abs" style="left:560px;top:3297px"><li>Home</li><li>About us</li><li>Services</li><li>Strategy</li></ul>
  <ul class="foot-links abs" style="left:731px;top:3297px"><li>Terms of Use</li><li>Privacy Policy</li><li>Site map</li></ul>

  <h4 class="foot-head abs" style="left:937px;top:3250px">Connect Us On</h4>
  <div class="social abs" style="left:938px;top:3306px"><span aria-label="Social profile"></span><span aria-label="Professional network profile"></span></div>

  <div class="bottom-rule abs"></div>
  <p class="copyright abs">Copyrights © 2019&nbsp; Bork Ventures. All rights reserved.</p>
  <p class="code abs">C16</p>
</footer>

</body>
</html>
```